Home Remodeling company needs a business card design

we need a business card design for home remodeling company in hamilton county, indiana USA. we offers a wide range of construction services including whole house renovations, Design and Build Basements and Kitchen and Bathroom Remodeling . we would like to see designs for both site of business card that use the same color of the company logo and also including all information below :
1- Karim Feltous CEO / General Contractor
2- all company contacts Telephone numbers ( 1-888-DULOM-47 ) ( 317-555-0193) email address ( info@dulomhome.com) website ( www.dulomhome.com ) and social media logos (Facebook- twitter- google plus )
3- company logo
4- licensed . insured . bonded

```html
<!DOCTYPE html>
<html lang="en">
<head>
<meta charset="utf-8">
<title>Dulom Home Remodeling – Business Card</title>
<link rel="stylesheet" href="https://fonts.googleapis.com/css2?family=Cabin:wght@400;500;600;700&display=swap">
<style>
  :root {
    --backdrop: #8e8f8f;
    --card-white: #e9e9eb;
    --ink: #2f2f31;
    --ink-soft: #3a3a3c;
    --brand-red: #a8282f;
    --band-dark: #333335;
    --white: #ffffff;
    --rule: #7a7a7c;
  }
  * { box-sizing: border-box; margin: 0; padding: 0; }
  html, body {
    width: 1105px; height: 1200px; overflow: hidden;
    background: var(--backdrop);
    font-family: "Cabin", "Gill Sans", sans-serif;
  }
  .canvas { position: relative; width: 1105px; height: 1200px; }
  .card {
    position: absolute; left: 182px; width: 746px; height: 427px; overflow: hidden;
  }
  .card--front { top: 119px; background: var(--card-white); }
  .card--back { top: 637px; background: var(--brand-red); }

  .company-name {
    position: absolute;
    font-size: 27px; font-weight: 600; line-height: 1; white-space: nowrap;
  }
  .card--front .company-name { left: 64px; top: 198px; color: var(--ink); }
  .card--back .company-name { left: 0; right: 0; text-align: center; top: 206px; color: var(--white); font-size: 32px; }

  .divider { position: absolute; left: 391px; top: 106px; width: 2px; height: 184px; background: var(--rule); }

  .person { position: absolute; left: 432px; top: 112px; }
  .person__name { font-size: 25px; font-weight: 600; color: var(--ink); }
  .person__title { font-size: 20px; color: var(--brand-red); margin-top: 4px; }

  .contacts { position: absolute; left: 432px; top: 182px; list-style: none; }
  .contacts li {
    display: flex; align-items: center; gap: 10px; height: 29px;
    font-size: 19px; color: var(--ink-soft);
  }
  .contacts svg { width: 16px; height: 16px; fill: var(--ink); flex: none; }

  .credentials-band {
    position: absolute; left: 0; right: 0; top: 380px; height: 47px;
    background: var(--band-dark);
    display: flex; align-items: center; justify-content: center;
    color: var(--white); font-size: 20px; letter-spacing: 0.5px;
    padding-right: 30px;
  }
  .credentials-band__accent {
    position: absolute; left: 0; top: 0; width: 11px; height: 47px; background: var(--brand-red);
    border-right: 3px solid var(--card-white);
  }
  .credentials-band__tip { position: absolute; right: 0; top: 0; width: 40px; height: 47px; }

  .social { position: absolute; left: 0; right: 0; top: 360px; display: flex; justify-content: center; align-items: center; gap: 6px; }
  .social__line { width: 60px; height: 1px; background: rgba(255,255,255,0.6); }
  .social__dot { width: 26px; height: 26px; border-radius: 50%; background: var(--card-white); }
</style>
</head>
<body>
<main class="canvas">

  <section class="card card--front" aria-label="Business card front">
    <p class="company-name">Dulom Home Remodeling</p>

    <div class="divider"></div>

    <div class="person">
      <p class="person__name">Karim Feltous</p>
      <p class="person__title">CEO / General Contractor</p>
    </div>

    <ul class="contacts">
      <li>
        <svg viewBox="0 0 24 24" aria-hidden="true"><path d="M6.6 10.8a15.1 15.1 0 0 0 6.6 6.6l2.2-2.2c.3-.3.7-.4 1-.2 1.1.4 2.3.6 3.6.6.6 0 1 .4 1 1V20c0 .6-.4 1-1 1A17 17 0 0 1 3 4c0-.6.4-1 1-1h3.5c.6 0 1 .4 1 1 0 1.3.2 2.5.6 3.6.1.3 0 .7-.2 1z"/></svg>
        1-888-DULOM-47
      </li>
      <li>
        <svg viewBox="0 0 24 24" aria-hidden="true"><path d="M7 1h10a2 2 0 0 1 2 2v18a2 2 0 0 1-2 2H7a2 2 0 0 1-2-2V3a2 2 0 0 1 2-2zm0 3v14h10V4z"/></svg>
        317-555-0193
      </li>
      <li>
        <svg viewBox="0 0 24 24" aria-hidden="true"><path d="M2 5h20v14H2zm2 2v.5l8 5 8-5V7zm0 2.8V17h16V9.8l-8 5z"/></svg>
        info@dulomhome.com
      </li>
      <li>
        <svg viewBox="0 0 24 24" aria-hidden="true"><circle cx="12" cy="12" r="10"/></svg>
        www.dulomhome.com
      </li>
    </ul>

    <div class="credentials-band">
      <span class="credentials-band__accent"></span>
      LICENSED | INSURED | BONDED
      <svg class="credentials-band__tip" viewBox="0 0 40 47" aria-hidden="true">
        <polygon points="40,0 40,47 8,23.5" fill="var(--card-white)"/>
        <rect x="24" y="18" width="11" height="11" fill="var(--brand-red)"/>
      </svg>
    </div>
  </section>

  <section class="card card--back" aria-label="Business card back">
    <p class="company-name">Dulom Home Remodeling</p>

    <div class="social" aria-label="Social media links">
      <span class="social__line"></span>
      <span class="social__dot"></span>
      <span class="social__dot"></span>
      <span class="social__dot"></span>
      <span class="social__line"></span>
    </div>
  </section>

</main>
</body>
</html>
```